Marlow Estate Fixers (Handyman / Home Improvement Company)

Looking for a double sided professional looking business card with Logo attached to be highlighted on one side and throwing in an image of a handyman as an option would be nice to see as well. We are a company focused on providing quality Handyman and Home improvement services in a timely manner that is done right the first time with integrity

Industry/Entity Type

Handyman / Home Improvement

Contact Information for Business Card

(LOGO, Name, Mobile and office phone numbers, email) on front side of card, (the words "The SOLUTION to all of your Handyman and Home Improvement needs" followed by "Family Owned and Operated" at the very bottom) on the back.

Colors
EB3D1F
EC4F4E
F09395
F8D3D4
FCEDEE

Requirements
Must have
• Red, Gray, Black Color scheme
Should not have
• No Yellow or Blue colors

```html
<!DOCTYPE html>
<html lang="en">
<head>
<meta charset="utf-8">
<title>Marlow Estate Fixers — Business Card</title>
<link rel="stylesheet" href="https://fonts.googleapis.com/css2?family=Krona+One&family=Poppins:wght@400;500&family=Oswald:wght@500&family=Playfair+Display:ital@0;1&display=swap">
<style>
  :root {
    --red: #e8262b;
    --red-soft: #ec4f4e;
    --black: #0b0b0b;
    --ink: #1a1a1a;
    --white: #ffffff;
    --stage: #d9d9db;
    --gray: #8a8a8a;
  }
  * { box-sizing: border-box; margin: 0; padding: 0; }
  html, body { width: 1200px; height: 866px; overflow: hidden; }
  body { background: var(--stage); position: relative; font-family: "Poppins", sans-serif; }

  .card {
    position: absolute;
    width: 700px;
    height: 400px;
    overflow: hidden;
    box-shadow: 0 10px 30px rgba(0,0,0,.25);
  }

  /* Front side */
  .card--front { left: 40px; top: 22px; background: var(--white); }
  .front__tab { position: absolute; left: 0; top: 52px; width: 36px; height: 20px; background: var(--red); }
  .front__name {
    position: absolute; left: 62px; top: 46px;
    font-family: "Krona One", sans-serif; font-size: 25px; letter-spacing: 1px;
    color: var(--red); text-transform: uppercase;
  }
  .front__contacts { position: absolute; left: 40px; top: 140px; width: 300px; list-style: none; }
  .front__contacts li {
    display: flex; align-items: center; gap: 12px;
    font-size: 19px; color: var(--ink); line-height: 34px; white-space: nowrap;
  }
  .front__contacts svg { width: 18px; height: 18px; flex: none; }
  .front__brand {
    position: absolute; right: 40px; top: 262px; width: 290px;
    display: flex; align-items: center; justify-content: flex-end; gap: 14px;
  }
  .front__brand-dot { width: 28px; height: 28px; border-radius: 50%; background: var(--red); flex: none; }
  .front__brand-name {
    font-family: "Krona One", sans-serif; font-size: 19px; line-height: 1.3;
    color: var(--black); text-transform: uppercase; letter-spacing: 1px;
  }
  .front__rule { position: absolute; left: 0; bottom: 26px; width: 360px; height: 5px; background: var(--red); }

  /* Back side */
  .card--back { left: 460px; top: 444px; background: var(--black); }
  .back__accent { position: absolute; inset: 0; }
  .back__figure {
    position: absolute; right: 40px; top: 50px; width: 250px; height: 320px;
    border-radius: 12px;
    background: linear-gradient(180deg, #3a3a3a 0%, #2a2a2a 100%);
  }
  .back__tagline {
    position: absolute; left: 40px; top: 92px; width: 380px;
    font-family: "Oswald", sans-serif; font-weight: 500; text-transform: uppercase;
    transform: skewX(-8deg); line-height: 1.12;
  }
  .back__lead { display: block; color: var(--white); font-size: 25px; }
  .back__focus { display: block; color: var(--red); font-size: 35px; }
  .back__footer {
    position: absolute; left: 40px; bottom: 46px;
    font-family: "Playfair Display", serif; font-size: 17px; color: var(--white);
  }
  .back__rule { position: absolute; left: 40px; bottom: 34px; width: 210px; height: 4px; background: var(--red); }
</style>
</head>
<body>

<section class="card card--front" aria-label="Business card front">
  <span class="front__tab"></span>
  <h1 class="front__name">Daniel Whitford</h1>
  <ul class="front__contacts">
    <li>
      <svg viewBox="0 0 20 20" aria-hidden="true"><rect x="5" y="1.5" width="10" height="17" rx="2" fill="none" stroke="var(--red)" stroke-width="2"/><circle cx="10" cy="15" r="1.2" fill="var(--red)"/></svg>
      044-555 018 342
    </li>
    <li>
      <svg viewBox="0 0 20 20" aria-hidden="true"><path d="M4 2h4l1.5 4-2.5 1.5a11 11 0 0 0 5.5 5.5L14 10.5l4 1.5v4a2 2 0 0 1-2 2C8.5 18 2 11.5 2 4a2 2 0 0 1 2-2z" fill="var(--red)"/></svg>
      044-555 018 342
    </li>
    <li>
      <svg viewBox="0 0 20 20" aria-hidden="true"><rect x="1" y="4" width="18" height="12" fill="var(--red)"/><path d="M1 4l9 7 9-7" fill="none" stroke="var(--white)" stroke-width="1.6"/></svg>
      hello@marlowfixers.com
    </li>
  </ul>
  <div class="front__brand">
    <span class="front__brand-dot"></span>
    <span class="front__brand-name">Marlow Estate<br>Fixers</span>
  </div>
  <span class="front__rule"></span>
</section>

<section class="card card--back" aria-label="Business card back">
  <svg class="back__accent" viewBox="0 0 700 400" preserveAspectRatio="none" aria-hidden="true">
    <polygon points="470,0 700,0 700,400 360,400" fill="var(--red)"/>
  </svg>
  <div class="back__figure" role="img" aria-label="Illustration of a cheerful handyman in a hard hat holding a power drill"></div>
  <p class="back__tagline">
    <span class="back__lead">Your solution to all of your</span>
    <span class="back__focus">Handyman and home<br>improvement needs</span>
  </p>
  <p class="back__footer">Family Owned and Operated</p>
  <span class="back__rule"></span>
</section>

</body>
</html>
```